2 x Digitize Logo | 2 x Business Cards | 2 x Fridge Magnets

We require 6 deliverables:
1. Residential logo redrawn (same just high quality for large print format).
2. Corporate logo redrawn (minor changes to wording and high quality for large print format).
3. New business card design for Furniture Removals (residential)
4. New business card design for Corporate Relocations (business)
5. New Fridge magnet for Furniture removals (residential)
6. New fridge magnet for Corporate Relocations (business)
1. Residential Logo
a. We require the logo to be translated into a high quality digital image with no modifications.
(see attached resilogo.jpg)
2. Residential Logo
a. We require the logo to be edited (add the word corporate relocations) be translated into a high quality digital image.
(see attached corplogo.jpg)
3. Using the resilogo please make a new business card for our business.
a. Please see the web site https://www.larkbendcarters.com.au for colours and inspiration.
b. The residential business card needs the following information:
i. Business Name (using the residential logo).
ii. Free Call: 1800 LB Cart (the L, B and Cart much be the same colour as the logo).
iii. Website: www.LarkbendCarters.com.au
iv. Address: 4/17 Ormsdale Court, VIC 3264
v. Email: cart@LarkbendCarters.com.au
vi. backof Card:
Review our service
www.PennantOrbit.com.au
Services: Local, Country, Interstate | Furniture Removals | Piano, Billiard Tables & Antiques
4. Using the corplogo please make a new business card for our business.
b. The corporate business card needs the following information:
i. Business Name (using the corporate logo).
v. Email: corporate@LarkbendCarters.com.au
vi. Back of Card:
Review our service
www.PennantOrbit.com.au
Services: Corporate relocations | Office equipment moves | Packing Service | Packing Materials
5. Using the resilogo please make a new fridge magent for our business.
b. The residential fidge magnet needs the following information:
iv. Services: Local, Country, Interstate | Furniture Removals | Piano, Billiard Tables & Antiques
6. Using the corplogo please make a new fridge magent for our business.
b. The corporate fidge magnet needs the following information:
iv. Services: Local, Country, Interstate | Corporate relocations
Target Market(s)
Residential Furniture Removals and Corporate Office relocations
Industry/Entity Type
Business
Contact Information for Business Card
Please see full brief for six items required
Requirements
Must have
- Clean simple, easy to read
Nice to have
- fresh, stand out, eye catching
Should not have
- plain, standard, boring, general

```html
<!DOCTYPE html>
<html lang="en">
<head>
<meta charset="utf-8">
<title>Larkbend Carters – Business Cards</title>
<link rel="stylesheet" href="https://fonts.googleapis.com/css2?family=Open+Sans:wght@400;700&family=Roboto+Condensed:wght@400;500;800&display=swap">
<style>
  :root {
    --backdrop: #cccccc;
    --card-dark: #2b2b2b;
    --card-light: #ffffff;
    --green: #0a9441;
    --red: #d7261f;
    --orange: #f0a21a;
    --ink: #2e2e2e;
    --ink-soft: #4a4a4a;
    --rule: #9a9a9a;
    --white: #ffffff;
  }
  * { box-sizing: border-box; margin: 0; padding: 0; }
  html, body { width: 1200px; height: 782px; overflow: hidden; background: var(--backdrop); }
  .sheet { position: relative; width: 1200px; height: 782px; }

  .card {
    position: absolute; width: 417px; height: 251px; overflow: hidden;
    box-shadow: 6px 8px 10px rgba(0,0,0,.28);
  }
  .card--dark { background: var(--card-dark); color: var(--white); }
  .card--light { background: var(--card-light); }
  .card--resi-back { left: 165px; top: 118px; }
  .card--resi-front { left: 617px; top: 118px; }
  .card--corp-back { left: 165px; top: 411px; }
  .card--corp-front { left: 617px; top: 411px; }

  .wordmark {
    position: absolute; font-family: "Roboto Condensed", sans-serif; font-weight: 800;
    color: var(--green); letter-spacing: .5px; line-height: 1; white-space: nowrap;
  }
  .wordmark--centre { left: 0; right: 0; text-align: center; }
  .tagline {
    position: absolute; font-family: "Open Sans", sans-serif; font-size: 10px;
    color: var(--green); line-height: 1; white-space: nowrap;
  }

  .review { position: absolute; left: 0; right: 0; text-align: center; font-family: "Open Sans", sans-serif; }
  .review__label {
    display: flex; align-items: center; justify-content: center; gap: 12px;
    font-size: 11px; color: #e8e8e8; line-height: 1;
  }
  .review__label::before, .review__label::after {
    content: ""; width: 88px; height: 2px;
    background: linear-gradient(90deg, transparent, var(--rule) 30%, var(--rule) 70%, transparent);
  }
  .review__url { margin-top: 6px; font-size: 15px; line-height: 1; color: var(--white); }
  .review__url .tone-orange { color: var(--orange); font-weight: 700; }
  .review__url .tone-green { color: var(--green); font-weight: 700; }

  .services {
    position: absolute; left: 0; right: 0; text-align: center;
    font-family: "Roboto Condensed", sans-serif; font-size: 10.5px; color: var(--white);
    white-space: nowrap; line-height: 1;
  }
  .services .sep { color: var(--orange); margin: 0 4px; }

  .wave { position: absolute; inset: 0; width: 100%; height: 100%; }

  .person { position: absolute; font-family: "Open Sans", sans-serif; color: var(--ink); }
  .person__name { font-size: 19px; font-weight: 700; line-height: 1; }
  .person__role { font-size: 10.5px; color: var(--ink-soft); margin-top: 6px; line-height: 1; }
  .person--right { right: 15px; text-align: right; }

  .contacts {
    position: absolute; right: 15px; top: 175px; list-style: none;
    font-family: "Roboto Condensed", sans-serif; font-size: 10.5px; color: var(--white);
    text-align: right; line-height: 15.5px;
  }
  .contacts li { display: flex; align-items: center; justify-content: flex-end; gap: 5px; }
  .contacts li.address { margin-top: 2px; }
  .contacts svg { width: 8px; height: 8px; fill: var(--white); }
</style>
</head>
<body>
<main class="sheet">

  <!-- Residential back -->
  <section class="card card--dark card--resi-back">
    <div class="wordmark wordmark--centre" style="top:58px;font-size:38px;">LARKBEND CARTERS</div>
    <div class="review" style="top:140px;">
      <p class="review__label">Review our service</p>
      <p class="review__url">www.<span class="tone-orange">Pennant</span><span class="tone-green">Orbit</span>.com.au</p>
    </div>
    <p class="services" style="top:225px;">Local, Country, Interstate<span class="sep">|</span>Furniture Removals<span class="sep">|</span>Piano, Billiard Tables &amp; Antiques</p>
  </section>

  <!-- Residential front -->
  <section class="card card--light card--resi-front">
    <svg class="wave" viewBox="0 0 521 314" preserveAspectRatio="none" aria-hidden="true">
      <path fill="var(--green)" d="M0 283 C160 300 330 250 521 160 L521 314 L0 314 Z"/>
      <path fill="var(--red)" d="M40 229 C160 262 310 236 521 137 L521 148 C310 252 170 272 40 229 Z"/>
      <path fill="var(--orange)" d="M0 220 C70 250 170 262 292 236 C190 268 80 280 0 272 Z"/>
    </svg>
    <div class="wordmark" style="left:24px;top:28px;font-size:39px;">LARKBEND CARTERS</div>
    <div class="person" style="left:27px;top:112px;">
      <p class="person__name">R. Hollis</p>
      <p class="person__role">Managing Director</p>
    </div>
    <ul class="contacts">
      <li>Free Call: 1800 LB Cart <svg viewBox="0 0 10 10"><path d="M1 4 Q5 0 9 4 L8 5 L6.5 4 V3 Q5 2.4 3.5 3 V4 L2 5 Z M2.5 5.5 H7.5 L8.5 9 H1.5 Z"/></svg></li>
      <li>LarkbendCarters.com.au <svg viewBox="0 0 10 10"><path d="M0 2 H10 V8 H0 Z M0.8 2.6 L5 5.6 L9.2 2.6" stroke="var(--green)" stroke-width=".8"/></svg></li>
      <li>cart@larkbendcarters.com.au <svg viewBox="0 0 10 10"><circle cx="5" cy="5" r="4.5"/><path d="M0.5 5 H9.5 M5 .5 V9.5 M5 .5 Q2 5 5 9.5 M5 .5 Q8 5 5 9.5" stroke="var(--green)" stroke-width=".7" fill="none"/></svg></li>
      <li class="address">4/17 Ormsdale Court, VIC 3264</li>
    </ul>
  </section>

  <!-- Corporate back -->
  <section class="card card--dark card--corp-back">
    <div class="wordmark wordmark--centre" style="top:75px;font-size:20px;">LARKBEND CARTERS</div>
    <p class="tagline" style="left:0;right:0;text-align:center;top:100px;">CORPORATE RELOCATIONS</p>
    <div class="review" style="top:178px;">
      <p class="review__label">Review our service</p>
      <p class="review__url">www.<span class="tone-orange">Pennant</span><span class="tone-green">Orbit</span>.com.au</p>
    </div>
    <p class="services" style="top:225px;">Corporate relocations<span class="sep">|</span>Office equipment moves<span class="sep">|</span>Packing Service<span class="sep">|</span>Packing Materials</p>
  </section>

  <!-- Corporate front -->
  <section class="card card--light card--corp-front">
    <svg class="wave" viewBox="0 0 521 314" preserveAspectRatio="none" aria-hidden="true">
      <path fill="var(--green)" d="M0 283 C160 300 330 250 521 160 L521 314 L0 314 Z"/>
      <path fill="var(--red)" d="M40 229 C160 262 310 236 521 137 L521 148 C310 252 170 272 40 229 Z"/>
      <path fill="var(--orange)" d="M0 220 C70 250 170 262 292 236 C190 268 80 280 0 272 Z"/>
    </svg>
    <div class="wordmark" style="left:22px;top:86px;font-size:21px;">LARKBEND CARTERS</div>
    <p class="tagline" style="left:39px;top:111px;">CORPORATE RELOCATIONS</p>
    <div class="person person--right" style="top:41px;">
      <p class="person__name">R. Hollis</p>
      <p class="person__role">Managing Director</p>
    </div>
    <ul class="contacts">
      <li>Free Call: 1800 LB Cart <svg viewBox="0 0 10 10"><path d="M1 4 Q5 0 9 4 L8 5 L6.5 4 V3 Q5 2.4 3.5 3 V4 L2 5 Z M2.5 5.5 H7.5 L8.5 9 H1.5 Z"/></svg></li>
      <li>LarkbendCarters.com.au <svg viewBox="0 0 10 10"><path d="M0 2 H10 V8 H0 Z M0.8 2.6 L5 5.6 L9.2 2.6" stroke="var(--green)" stroke-width=".8"/></svg></li>
      <li>corporate@larkbendcarters.com.au <svg viewBox="0 0 10 10"><circle cx="5" cy="5" r="4.5"/><path d="M0.5 5 H9.5 M5 .5 V9.5 M5 .5 Q2 5 5 9.5 M5 .5 Q8 5 5 9.5" stroke="var(--green)" stroke-width=".7" fill="none"/></svg></li>
      <li class="address">4/17 Ormsdale Court, VIC 3264</li>
    </ul>
  </section>

</main>
</body>
</html>
```